Brand new letterhead, business card, email signature etc.

We are a financial company in London, UK. Our website is www.marlowvane.com. We're wanting a complete remodel of the company colours, letter head, business cards, email signatures, etc. Looking to keep the same font for the company name. I have upload a colour palette that we want to work with. We're looking for company letterhead for outgoing letters/ correspondence, letterhead for internal documentation, email signatures, e-letters. etc. Ultimately we will redesign the entire website also. It is important that our clients get a strong, secure, warm, trustworthy, solid feeling and first impression.
Updates

Designs look the same

Target Market(s)

Institutional investors, (ultra) high net worth individuals

Industry/Entity Type

Finance, Invesments banking.

Font styles to use
Other font styles liked:
• Current font is "Champagne & Limousines"

Requirements
Must have
• Must use the colours provided on the PDF uploaded to the portal. The purple = main colour. The red = accent colour.
Nice to have
• Nice to use same font as now for the company name "Corvane". Font is "Champagne & Limousines". Nice to have some reference to the old logo flower, but only subtle.
Should not have
• Do not use the colour red from our website. Use the colours provided on the colour palette PDF that I uploaded in the portal.

```html
<!DOCTYPE html>
<html lang="en">
<head>
<meta charset="utf-8">
<title>Corvane — Business Card</title>
<link rel="stylesheet" href="https://fonts.googleapis.com/css2?family=Didact+Gothic&family=Josefin+Sans:wght@300&family=Montserrat:wght@700&display=swap">
<style>
  :root {
    --page-bg: #d8ccbb;
    --plum-deep: #22090f;
    --plum-mid: #2e1219;
    --plum-light: #43272e;
    --accent-red: #c4352a;
    --cream: #d8c9b4;
    --cream-soft: #bfae98;
    --card-edge: #cbbca6;
  }
  * { margin: 0; padding: 0; box-sizing: border-box; }
  html, body {
    width: 1200px; height: 1046px; overflow: hidden;
    background: var(--page-bg);
  }
  .business-card {
    position: absolute; left: 50px; top: 224px;
    width: 1100px; height: 598px;
    background:
      radial-gradient(ellipse 420px 300px at 300px 330px, var(--plum-light), transparent 75%),
      linear-gradient(100deg, var(--plum-mid) 0%, var(--plum-deep) 55%, #2f151c 100%);
    border: 2px solid var(--card-edge);
    box-shadow: 0 10px 30px rgba(40, 20, 20, 0.25);
    overflow: hidden;
  }
  .brand-mark {
    position: absolute; left: 34px; top: 27px;
    width: 126px; height: 122px;
    border: 1.5px solid var(--cream-soft);
  }
  .brand-name {
    position: absolute; left: 192px; top: 48px;
    font-family: "Josefin Sans", sans-serif; font-weight: 300;
    font-size: 70px; letter-spacing: 16px; line-height: 1;
    color: var(--cream);
  }
  .flower-decoration {
    position: absolute; left: 610px; top: 95px;
    width: 480px; height: 500px;
    background: radial-gradient(ellipse at 55% 55%, rgba(120, 28, 24, 0.35), rgba(90, 20, 20, 0.12) 55%, transparent 75%);
  }
  .holder-name {
    position: absolute; left: 38px; top: 387px;
    font-family: "Montserrat", sans-serif; font-weight: 700;
    font-size: 46px; line-height: 1; letter-spacing: 0.5px;
    color: var(--cream);
  }
  .holder-name .first-name { color: var(--accent-red); }
  .holder-title {
    font-family: "Didact Gothic", sans-serif; font-weight: 400;
    font-size: 30px; color: var(--accent-red); margin-left: 12px;
  }
  .contact-row, .address-line {
    position: absolute; left: 38px;
    font-family: "Didact Gothic", sans-serif;
    font-size: 27px; line-height: 1; color: var(--cream);
    white-space: nowrap;
  }
  .contact-row { top: 466px; width: 1030px; }
  .contact-item { position: absolute; top: 0; }
  .contact-item .label { color: var(--accent-red); }
  .contact-phone { left: 0; }
  .contact-email { left: 362px; }
  .contact-web { left: 735px; }
  .address-line { top: 518px; color: var(--cream-soft); }
  .accent-rule {
    position: absolute; left: 0; right: 0; bottom: 4px;
    height: 3px; background: var(--accent-red);
  }
</style>
</head>
<body>
  <div class="business-card">
    <div class="brand-mark"></div>
    <div class="brand-name">CORVANE</div>

    <div class="flower-decoration" role="img" aria-label="Large outlined flower decoration in deep red"></div>

    <div class="holder-name">
      <span class="first-name">Elena</span> Varkova<span class="holder-title">CEO</span>
    </div>

    <div class="contact-row">
      <span class="contact-item contact-phone"><span class="label">T:</span> (555) 014-2276</span>
      <span class="contact-item contact-email"><span class="label">E:</span> info@marlowvane.com</span>
      <span class="contact-item contact-web"><span class="label">W:</span> www.marlowvane.com</span>
    </div>

    <div class="address-line">Corvane (IOM) Limited, Ardley House, Douglas, Isle of Man, IM8 4QT</div>

    <div class="accent-rule"></div>
  </div>
</body>
</html>
```